AWESOME RETAILER OF PHONE ACCESSORIES NEEDS AWESOME WEBSITE FROM AWESOME DESIGNER

We currently do not have any website and are looking for one for our new store. We are a retailer who sells tuvaset accessories, speakers, electronics, cables with the best pricing guaranteed. We carry all top name brands including:

TrailShell : http://www.trailshell-example.com/en/

Harecase : http://www.harecase-example.com/

Kelvra : http://www.kelvra-example.com/Default.asp

Davoren : http://www.davoren-example.com/

Tidy Kit : http://www.tidy-kit-example.com/

http://www.glassmantle-example.com/hot-sellers/handset-model-crystl-white.html

http://www.velmarworks-example.com/products/detail.cfm?prodID=2

http://gristcam-example.com/

http://www.quobb-example.com/

We would like to see our logo's used and a website that is trendy and catchy to our demographics. Our demographic is male/female between the ages of 16-45.

Target Market(s)

Male/Femal Ages -16-45

Industry/Entity Type

Electronics

Requirements
Must have
• Must use our logo's and be a catchy fun website keeps the customers eye.
Coupon Tab where customers can print coupons
Products Tab where we can display all of our brands of products
Contact us page
Location Page
FRIENDLOOP/CHIRPNET ACCOUNT TO BE LINKED TO SITE
WEBSITE WILL BE HOSTED BY HOSTWREN-EXAMPLE.COM PLEASE MAKE SURE YOUR DESIGN IS COMPATIBLE WITH THEM.

PLEASE BE SURE TO USE OUR LOGO IN YOUR DESIGN YOU SUBMIT, THEY ARE ATTACHED TO THIS PROJECT
Nice to have
• We would like a slot where a video can be posted from clipvault
Authorized dealer banner
Should not have
• not a dark website but bright and vibrant
Do not use any logos or images that are trademarked by Plumtree.

```html
<!DOCTYPE html>
<html lang="en">
<head>
<meta charset="utf-8">
<title>Vantocell – Phone Accessories</title>
<link rel="stylesheet" href="https://fonts.googleapis.com/css2?family=Oswald:wght@400;500&family=Open+Sans:wght@400;600&family=Arimo:wght@400;700&family=Questrial&display=swap">
<style>
:root{
  --green:#9dc83c;
  --green-footer:#99cc00;
  --green-logo:#8cc63f;
  --dark:#3d3d3d;
  --nav-active:#2b2b2b;
  --grey-btn:#8e8e8e;
  --text:#555555;
  --link:#1a84c7;
  --line:#d6d6d6;
  --white:#ffffff;
}
*{box-sizing:border-box;margin:0;padding:0}
html,body{width:1200px;height:1000px;overflow:hidden;background:var(--white)}
body{position:relative;font-family:"Arimo",Arial,sans-serif;color:var(--text)}
.abs{position:absolute}

.brand{left:260px;top:14px;display:flex;align-items:center;gap:10px}
.brand-mark{width:22px;height:22px;border-radius:50%;background:var(--green-logo)}
.brand-name{font-family:"Open Sans",sans-serif;font-weight:600;font-size:38px;color:var(--green-logo);line-height:1}

.main-nav{left:91px;top:98px;width:1007px;height:32px;background:var(--green);box-shadow:0 3px 4px rgba(0,0,0,.12)}
.nav-list{position:absolute;left:111px;top:0;display:flex;list-style:none;height:32px;border-left:1px solid #6e8f2a}
.nav-list li{font-family:"Oswald",sans-serif;font-size:13px;color:var(--white);height:32px;line-height:32px;padding:0 12px;border-right:1px solid #6e8f2a;text-shadow:0 1px 1px rgba(0,0,0,.35)}
.nav-list li.active{background:var(--nav-active);color:#cfcfcf}
.search-field{left:804px;top:102px;width:122px;height:25px;border-radius:13px;background:var(--white);border:1px solid #c9c9c9;font-size:12px;color:#333;padding:5px 12px}
.search-btn{left:930px;top:102px;width:57px;height:25px;border-radius:3px;background:linear-gradient(#a9a9a9,#7d7d7d);color:var(--white);font-family:"Oswald",sans-serif;font-size:12px;text-align:center;line-height:25px}

.slider{left:202px;top:135px;width:785px;height:335px;background:var(--white);overflow:hidden}
.slide-title{position:absolute;left:38px;top:10px;font-family:"Questrial",sans-serif;font-size:76px;color:#8dc63f;letter-spacing:1px}
.slide-desc{position:absolute;left:37px;top:128px;width:280px;font-family:"Questrial",sans-serif;font-size:15px;line-height:21px;color:#9a9a9a}
.slide-photo{position:absolute;left:438px;top:15px;width:296px;height:318px;border-radius:50% 50% 40% 40% / 30% 30% 20% 20%;background:radial-gradient(ellipse at 50% 70%,#4a4a4a 0%,#1e1e1e 60%,#e6e6e6 100%)}
.arrow{position:absolute;width:33px;height:33px;border-radius:50%;background:#8a8a8a;color:var(--white);font-size:22px;text-align:center;line-height:31px}
.caption{position:absolute;left:0;top:266px;width:785px;height:69px;background:rgba(40,40,40,.9);color:var(--white);padding:9px 12px}
.caption h2{font-family:"Oswald",sans-serif;font-weight:400;font-size:18px;margin-bottom:8px}
.caption p{font-size:11px}

.panel{border:1px solid var(--line);background:var(--white)}
.panel-head{height:26px;background:var(--green);color:var(--white);font-family:"Oswald",sans-serif;font-size:12.5px;letter-spacing:.5px;line-height:26px;padding-left:8px}
.latest{left:202px;top:495px;width:182px;height:228px}
.product-photo{position:absolute;left:22px;top:34px;width:136px;height:160px;background:linear-gradient(180deg,#f4f4f4,#dcdcdc)}
.product-caption{position:absolute;left:4px;top:153px;width:172px;height:53px;background:rgba(40,40,40,.88);color:var(--white);font-family:"Oswald",sans-serif;font-size:17px;line-height:42px;padding-left:13px}

.intro{left:403px;top:495px;width:384px;font-size:11px;line-height:19.3px;color:var(--text)}

.login{left:806px;top:495px;width:182px;height:273px}
.login-body{padding:9px 4px;font-size:10.5px;color:#444}
.field-label{margin:0 0 5px 1px}
.field{display:flex;width:145px;height:24px;border:1px solid #c6c6c6;border-radius:3px;margin-bottom:10px;overflow:hidden}
.field-icon{width:21px;background:#eeeeee;border-right:1px solid #c6c6c6;display:flex;align-items:center;justify-content:center}
.field span{padding:5px;color:#aaa;font-size:10.5px}
.remember{display:flex;align-items:center;gap:5px;margin:-2px 0 7px}
.remember i{width:10px;height:10px;border:1px solid #999;display:block}
.login-btn{width:52px;height:23px;border-radius:3px;background:linear-gradient(#9b9b9b,#777);color:var(--white);font-family:"Oswald",sans-serif;font-size:11px;text-align:center;line-height:23px;margin-bottom:9px}
.login-links{list-style:none;padding-left:14px}
.login-links li{display:flex;align-items:center;gap:9px;color:var(--link);font-size:11px;height:19px}

.tagline{left:0;top:770px;width:1200px;text-align:center;font-family:"Open Sans",sans-serif;font-weight:600;font-size:26px;color:#1a1a1a;letter-spacing:-.3px}
.tagline em{font-style:normal;color:var(--green-logo)}

.site-footer{left:91px;top:826px;width:1007px;height:108px;background:var(--green-footer);border-top:1px solid #555}
.social{position:absolute;left:112px;top:17px;display:flex;gap:6px}
.social span{height:30px;padding:0 6px;border-radius:3px;background:rgba(255,255,255,.25);color:var(--white);font-size:10px;line-height:30px;font-family:"Arimo",sans-serif}
.copyright{position:absolute;left:111px;top:69px;font-size:9.5px;color:var(--white);text-shadow:1px 1px 1px #333}
.to-top{position:absolute;left:952px;top:52px;width:28px;height:28px;border-radius:4px;background:#7fa33a;display:flex;align-items:center;justify-content:center}
</style>
</head>
<body>

<div class="brand abs"><span class="brand-mark"></span><span class="brand-name">Vantocell</span></div>

<nav class="main-nav abs">
  <ul class="nav-list">
    <li class="active">HOME</li><li>PRODUCTS</li><li>ABOUT US</li><li>SIGN UP</li><li>CONTACT US</li>
  </ul>
</nav>
<div class="search-field abs">Search...</div>
<div class="search-btn abs">SEARCH</div>

<section class="slider abs">
  <div class="slide-title">electronics</div>
  <p class="slide-desc">Description about cables which sell by vantocell.Description about cables which sell by vantocell.Description about cables which sell by vantocell.</p>
  <div class="slide-photo" role="img" aria-label="Smartphone docked on a round black speaker"></div>
  <div class="arrow" style="left:14px;top:117px">&#10094;</div>
  <div class="arrow" style="left:738px;top:117px">&#10095;</div>
  <div class="caption">
    <h2>Electronics</h2>
    <p>Pellentesque habitant morbi tristique senectus et netus et malesuada fames ac turpis egestas. In posuere felis nec tortor. Pellentesque faucibus.</p>
  </div>
</section>

<aside class="latest panel abs">
  <div class="panel-head">LATEST PRODUCTS</div>
  <div class="product-photo" role="img" aria-label="White charging cable coiled"></div>
  <div class="arrow" style="left:19px;top:89px">&#10094;</div>
  <div class="arrow" style="left:128px;top:89px">&#10095;</div>
  <div class="product-caption">Product 5</div>
</aside>

<p class="intro abs">Phasellus felis dolor, scelerisque a, tempus eget, lobortis id, libero. Donec scelerisque leo ac risus. Praesent sit amet est. In dictum, dolor eu dictum porttitor, enim felis viverra mi, eget luctus massa purus quis odio. Etiam nulla massa, pharetra facilisis, volutpat in, imperdiet sit amet, sem. Aliquam nec erat at purus cursus interdum. Vestibulum ligula augue, bibendum accumsan, vestibulum ut, commodo a, mi. Morbi ornare gravida elit. Integer congue, augue et malesuada iaculis, ipsum dui aliquet felis, at cursus magna nisl nec elit. Donec iaculis diam a nisi accumsan viverra. Duis sed tellus et tortor vestibulum gravida. Praesent elementum elit at tellus. Curabitur metus ipsum, luctus eu, malesuada ut, tincidunt sed, diam. Donec quis mi sed magna hendrerit accumsan. Suspendisse risus nibh, ultricies eu, volutpat non, condimentum hendrerit, augue. Etiam eleifend, metus vitae adipiscing semper, purus ipsum iaculis elit, congue gravida elit mi egestas orci. Curabitur pede.</p>

<aside class="login panel abs">
  <div class="panel-head">LOGIN</div>
  <div class="login-body">
    <p class="field-label">User Name</p>
    <div class="field"><div class="field-icon"><svg width="10" height="11" viewBox="0 0 10 11"><circle cx="5" cy="3" r="2.6" fill="#888"/><path d="M0 11c0-4 2-5.5 5-5.5s5 1.5 5 5.5z" fill="#888"/></svg></div><span>User Name</span></div>
    <p class="field-label">Password</p>
    <div class="field"><div class="field-icon"><svg width="9" height="11" viewBox="0 0 9 11"><path d="M2 5V3.5a2.5 2.5 0 0 1 5 0V5" stroke="#888" stroke-width="1.4" fill="none"/><rect x="0" y="5" width="9" height="6" fill="#888"/></svg></div><span>Password</span></div>
    <div class="remember"><i></i>Remember Me</div>
    <div class="login-btn">LOG IN</div>
    <ul class="login-links">
      <li><svg width="9" height="10" viewBox="0 0 9 11"><path d="M2 5V3.5a2.5 2.5 0 0 1 5 0V5" stroke="#777" stroke-width="1.4" fill="none"/><rect y="5" width="9" height="6" fill="#777"/></svg>Forgot your password?</li>
      <li><svg width="9" height="10" viewBox="0 0 10 11"><circle cx="5" cy="3" r="2.6" fill="#777"/><path d="M0 11c0-4 2-5.5 5-5.5s5 1.5 5 5.5z" fill="#777"/></svg>Forgot your username?</li>
      <li><svg width="10" height="10" viewBox="0 0 10 10"><rect x=".5" y="1.5" width="8" height="8" fill="none" stroke="#777"/><path d="M2.5 5l2 2 5-6" stroke="#777" stroke-width="1.4" fill="none"/></svg>Create an account</li>
    </ul>
  </div>
</aside>

<p class="tagline abs">SEE HOW PEOPLE LIVE IN <em>DIFFERENT</em> LIFE STYLE</p>

<footer class="site-footer abs">
  <div class="social"><span>Friendloop</span><span>Chirpnet</span><span>Clipvault</span><span>Linkwell</span></div>
  <p class="copyright">Copyrights By Vantocell 2013</p>
  <div class="to-top"><svg width="14" height="9" viewBox="0 0 14 9"><path d="M1 8l6-6 6 6" stroke="#fff" stroke-width="2.2" fill="none"/></svg></div>
</footer>

</body>
</html>
```